Business Card and Letterhead for Pimlu - modern real estate business

I need a double sided business card design for Pimlu. Please see business card brief here https://files.trelvonadocs.com/sheet/r/7QzTmWbaXLJnoPEd-kRyUgFhHsstbvCe2qfoMxDa_pz/view?mode=shared

Please feel free to design the business cards however you feel best. I am happy to give some creative freedoms and then provide feedback from there.

Please then also create a letterhead to match the business card design

Colors

Designer to choose colors to be used in the design.

Requirements
Must have
• Must be a modern, elegant business card which looks very professional

```html
<!DOCTYPE html>
<html lang="en">
<head>
<meta charset="utf-8">
<title>Pimlu – Letterhead and Business Card</title>
<link href="https://fonts.googleapis.com/css2?family=Lato:wght@400;700;900&display=swap" rel="stylesheet">
<style>
:root{
  --brand-red:#e3222a;
  --ink:#141414;
  --paper:#ffffff;
  --backdrop:#e8e5e1;
  --text:#1c1c1c;
  --photo-tone:#8a8f86;
  --photo-tone-soft:#a9ada4;
}
*{margin:0;padding:0;box-sizing:border-box}
html,body{width:1200px;height:900px;overflow:hidden}
body{background:var(--backdrop);font-family:'Lato',sans-serif;color:var(--text);position:relative}

.letterhead{position:absolute;left:132px;top:112px;width:493px;height:698px;background:var(--paper);box-shadow:0 3px 10px rgba(0,0,0,.25);overflow:hidden}
.letterhead__header{position:absolute;left:0;top:0;width:493px;height:80px}
.letterhead__brand{position:absolute;left:16px;top:48px;font-weight:900;font-size:40px;letter-spacing:6px;color:var(--brand-red);line-height:1}
.letter{position:absolute;left:47px;top:176px;width:401px;font-size:9.6px;line-height:12px}
.letter p{text-align:justify;margin-bottom:23.5px}
.letter__greeting{margin-bottom:17px !important}
.letter__signoff{position:absolute;left:47px;top:482px;font-size:9.6px;line-height:13.2px}
.letterhead__footer{position:absolute;left:0;bottom:0;width:100%;height:27px;background:var(--ink);color:#fff;font-size:9.8px;display:flex;align-items:center;justify-content:center;gap:8px}

.card{position:absolute;width:408px;height:246px;box-shadow:0 3px 10px rgba(0,0,0,.3)}
.card--front{left:714px;top:170px;background:var(--paper)}
.card--back{left:712px;top:461px;height:248px;background:var(--ink);display:flex;align-items:center;justify-content:center}
.card__photo{position:absolute;left:35px;top:51px;width:142px;height:142px;border-radius:50%;border:2px solid var(--brand-red);background:linear-gradient(180deg,var(--photo-tone-soft),var(--photo-tone))}
.card__divider{position:absolute;left:203px;top:50px;width:1.5px;height:144px;background:var(--brand-red)}
.card__details{position:absolute;left:227px;top:53px;font-size:11.4px;line-height:13.8px}
.card__name{font-size:18.5px;font-weight:900;color:var(--brand-red);line-height:22px}
.card__title{margin-top:1px}
.card__address{margin-top:11px}
.card__contacts{margin-top:12px;list-style:none}
.card__contacts li{display:flex;align-items:center;gap:8px;height:15.6px}
.card__contacts svg{width:11px;height:11px;flex:none}
.card__brand{font-weight:900;font-size:76px;letter-spacing:14px;margin-right:-14px;color:var(--brand-red);line-height:1}
</style>
</head>
<body>

<section class="letterhead">
  <svg class="letterhead__header" viewBox="0 0 493 80" aria-hidden="true">
    <path d="M0 0 H493 V76 C380 30 200 17 0 17 Z" fill="var(--ink)"/>
    <path d="M0 21 C190 20 360 30 470 70 C355 38 190 30 0 32 Z" fill="var(--brand-red)"/>
  </svg>
  <div class="letterhead__brand">PIMLU</div>

  <div class="letter">
    <p class="letter__greeting">Dear Sir/Mam,</p>
    <p>Contrary to popular belief, Lorem Ipsum is not simply random text. It has roots in a piece of classical Latin literature from 45 BC, making it over 2000 years old. Daniel Wrenfield, a Latin professor at Corbel Ridge College in Vermara, looked up one of the more obscure Latin words, consectetur, from a Lorem Ipsum passage, and going through the cites of the word in classical literature, discovered the undoubtable source.</p>
    <p>Lorem Ipsum comes from sections 1.10.32 and 1.10.33 of "de Finibus Bonorum et Malorum" (The Extremes of Good and Evil) by Varenus, written in 45 BC. This book is a treatise on the theory of ethics, very popular during the Renaissance. The first line of Lorem Ipsum, "Lorem ipsum dolor sit amet..", comes from a line in section 1.10.32.</p>
    <p>The standard chunk of Lorem Ipsum used since the 1500s is reproduced below for those interested. Sections 1.10.32 and 1.10.33 from "de Finibus Bonorum et Malorum" by Varenus are also reproduced in their exact original form, accompanied by English versions from the 1914 translation by H. Dellmore.</p>
    <p>The standard chunk of Lorem Ipsum used since the 1500s is reproduced below for those interested.</p>
  </div>
  <div class="letter__signoff">Best Regards<br>Liam Carter<br>Licenced Real Estate Agent</div>

  <footer class="letterhead__footer">
    <span>0400 318 952</span><span>|</span><span>liam@pimlu.com</span><span>|</span><span>www.pimlu.com</span><span>|</span><span>PO Box 3190. Larkvale NSW 2790</span>
  </footer>
</section>

<section class="card card--front">
  <div class="card__photo" role="img" aria-label="Portrait photo of the agent"></div>
  <div class="card__divider"></div>
  <div class="card__details">
    <div class="card__name">Liam Carter</div>
    <div class="card__title">Licenced Real Estate Agent</div>
    <div class="card__address">PO Box 3190<br>Larkvale NSW 2790</div>
    <ul class="card__contacts">
      <li><svg viewBox="0 0 12 12" aria-hidden="true"><path d="M2.5 1 L4.5 1 L5.3 3.6 L4 4.6 C4.7 6 5.9 7.3 7.4 8 L8.4 6.7 L11 7.5 L11 9.5 C11 10.3 10.3 11 9.5 11 C5 10.7 1.3 7 1 2.5 C1 1.7 1.7 1 2.5 1 Z" fill="var(--brand-red)"/></svg>0400 318 952</li>
      <li><svg viewBox="0 0 12 12" aria-hidden="true"><rect x="0.5" y="2.5" width="11" height="7.5" fill="var(--brand-red)"/><path d="M0.8 2.8 L6 6.8 L11.2 2.8" stroke="#fff" stroke-width="1" fill="none"/></svg>liam@pimlu.com</li>
      <li><svg viewBox="0 0 12 12" aria-hidden="true"><g fill="none" stroke="var(--brand-red)" stroke-width="0.9"><circle cx="6" cy="6" r="5"/><ellipse cx="6" cy="6" rx="2.2" ry="5"/><path d="M1 6 H11 M2 3.3 H10 M2 8.7 H10"/></g></svg>www.pimlu.com</li>
    </ul>
  </div>
</section>

<section class="card card--back">
  <div class="card__brand">PIMLU</div>
</section>

</body>
</html>
```